Business Card Design for a Personal Trainer

I need a business card design for my job as a personal trainer. It should have a unique, modern and exclusive design. On the front there should be only my logo with my name and my job. 0162/3819204 Tobias Lendhart Wiesengrundweg 14 80417 Munich Germany The most important contact information is the web adress. it can be bigger than the rest, but its not necessary. The card should be 8,5cmx5,5cm big. Font: Roboto. Colors: black, white, gray, 56c1ff.

```html
<!DOCTYPE html>
<html lang="de">
<head>
<meta charset="utf-8">
<title>Tobias Lendhart – Personal Trainer Visitenkarte</title>
<link href="https://fonts.googleapis.com/css2?family=Roboto:wght@300;400;500;700&display=swap" rel="stylesheet">
<style>
  :root {
    --sky: #56c1ff;
    --sky-deep: #3aaef8;
    --ink: #111111;
    --steel: #8a8a8a;
    --mist: #c4c4c4;
    --paper: #ffffff;
    --stage-light: #8c8c8c;
    --stage-dark: #3f3f3f;
  }
  * { margin: 0; padding: 0; box-sizing: border-box; }
  html, body { width: 1200px; height: 1200px; overflow: hidden; }
  body {
    font-family: 'Roboto', sans-serif;
    background: radial-gradient(circle at 50% 50%, var(--stage-light), var(--stage-dark) 75%);
    position: relative;
  }
  .card {
    position: absolute;
    width: 640px;
    height: 414px;
    overflow: hidden;
    box-shadow: 0 18px 40px rgba(0,0,0,0.35);
  }

  /* Logo side */
  .card--logo {
    left: 480px; top: 120px;
    background: linear-gradient(135deg, var(--sky), #62c8ff 50%, var(--sky-deep));
  }
  .card--logo .frame {
    position: absolute; inset: 24px;
    border: 2px solid var(--paper);
  }
  .brand {
    position: absolute; left: 0; right: 0; top: 140px;
    text-align: center; color: var(--paper);
  }
  .brand__mark {
    display: inline-block; width: 22px; height: 22px;
    background: var(--paper); margin-bottom: 14px;
  }
  .brand__name {
    font-weight: 300; font-size: 40px; letter-spacing: 2px;
  }
  .brand__job {
    display: flex; align-items: center; justify-content: center; gap: 14px;
    font-weight: 300; font-size: 15px; letter-spacing: 6px; margin-top: 6px;
  }
  .brand__job::before, .brand__job::after {
    content: ""; width: 60px; height: 1px; background: var(--paper);
  }
  .card--logo .web {
    position: absolute; left: 60px; bottom: 14px;
    padding: 0 12px;
    background: linear-gradient(90deg, #5cc4ff, #4fbcff);
    font-weight: 700; font-size: 22px; color: var(--ink);
  }

  /* Contact side */
  .card--contact {
    left: 80px; top: 640px;
    background: var(--paper);
  }
  .card--contact svg.waves { position: absolute; inset: 0; }
  .portrait {
    position: absolute; left: 360px; top: 170px; width: 230px; height: 244px;
    background: linear-gradient(180deg, #9a9a9a, #4a4a4a);
  }
  .holder-name {
    position: absolute; left: 34px; top: 22px;
    font-weight: 700; font-size: 44px; color: var(--ink);
  }
  .holder-name span { color: var(--steel); }
  .contact {
    position: absolute; left: 30px; top: 150px;
    color: var(--paper); font-size: 16px; line-height: 1.45;
  }
  .contact__address { font-weight: 700; margin-bottom: 4px; }
  .contact__row { display: flex; align-items: center; gap: 8px; font-weight: 400; }
  .contact__row svg { width: 16px; height: 16px; flex: none; }
  .card--contact .web {
    position: absolute; left: 30px; top: 300px;
    font-weight: 700; font-size: 26px; color: var(--paper);
  }
</style>
</head>
<body>

  <section class="card card--logo" aria-label="Visitenkarte Vorderseite">
    <div class="frame"></div>
    <div class="brand">
      <span class="brand__mark"></span>
      <div class="brand__name">TOBIAS LENDHART</div>
      <div class="brand__job">PERSONAL TRAINER</div>
    </div>
    <div class="web">www.tobiaslendhart.de</div>
  </section>

  <section class="card card--contact" aria-label="Visitenkarte Rückseite">
    <svg class="waves" width="640" height="414" viewBox="0 0 640 414">
      <defs>
        <linearGradient id="skyFill" x1="0" y1="0" x2="1" y2="1">
          <stop offset="0" stop-color="#5fc6ff"/>
          <stop offset="1" stop-color="#3aaef8"/>
        </linearGradient>
      </defs>
      <path d="M0,88 C190,78 280,150 320,260 S400,414 500,414 L0,414 Z" fill="#111111"/>
      <path d="M0,104 C180,96 262,164 302,270 S380,414 480,414 L0,414 Z" fill="#c4c4c4"/>
      <path d="M0,126 C170,118 244,180 282,282 S360,414 450,414 L0,414 Z" fill="url(#skyFill)"/>
    </svg>

    <div class="portrait" role="img" aria-label="Schwarzweißfoto des Trainers mit verschränkten Armen"></div>

    <h1 class="holder-name">Tobias <span>Lendhart</span></h1>

    <div class="contact">
      <div class="contact__address">Wiesengrundweg 14<br>80417 München</div>
      <div class="contact__row">
        <svg viewBox="0 0 16 16"><circle cx="8" cy="8" r="7" fill="none" stroke="#fff" stroke-width="1.4"/><path d="M5.5 4.5l1.5 1.6-0.8 1.2c0.5 1 1.3 1.8 2.3 2.3l1.2-0.8 1.6 1.5-1 1.2c-2.6-0.4-4.8-2.6-5.2-5.2z" fill="#fff"/></svg>
        0162/3819204
      </div>
      <div class="contact__row">
        <svg viewBox="0 0 16 16"><circle cx="8" cy="8" r="7" fill="none" stroke="#fff" stroke-width="1.4"/><rect x="4.3" y="5.3" width="7.4" height="5.4" fill="none" stroke="#fff" stroke-width="1.1"/><path d="M4.3 5.5L8 8.3l3.7-2.8" fill="none" stroke="#fff" stroke-width="1.1"/></svg>
        t.lendhart@mailbox.de
      </div>
    </div>

    <div class="web">www.tobiaslendhart.de</div>
  </section>

</body>
</html>
```